Specialised investor in e-mobility and energy wants business card design

We need a business card design that fits our existing corporate design. <The look and feel must be 'sharp'/'clean', dynamic, communicate momentum, professionalism etc (as one would imagine from a firm in the financial sector). We like the idea of a reverse-side of the card that includes the logo, and the name and contact details on the other. We expect the deliverable to be whatever format might be required to be able to get cards printed directly by a service such as kelmo press. Our website is www.zub.capital

```html
<!DOCTYPE html>
<html lang="en">
<head>
<meta charset="utf-8">
<title>Zub Capital – Business Card</title>
<link rel="stylesheet" href="https://fonts.googleapis.com/css2?family=Questrial&family=Mulish:wght@700&display=swap">
<style>
  :root {
    --backdrop: #e4e4e4;
    --paper: #f5f5f5;
    --forest: #2e4722;
    --forest-text: #2f4a22;
    --ink-grey: #555a55;
    --divider: #b9bcb7;
  }
  html, body {
    margin: 0;
    padding: 0;
    width: 1200px;
    height: 1200px;
    overflow: hidden;
    background: var(--backdrop);
  }
  .canvas {
    position: relative;
    width: 1200px;
    height: 1200px;
    font-family: "Questrial", "Century Gothic", sans-serif;
  }
  .card {
    position: absolute;
    left: 262px;
    width: 686px;
    height: 392px;
    border-radius: 21px;
  }
  .card--front { top: 165px; background: var(--paper); }
  .card--back  { top: 653px; background: var(--forest); }

  .wordmark {
    position: absolute;
    white-space: nowrap;
    font-family: "Questrial", sans-serif;
    font-weight: 400;
    line-height: 1;
  }
  .card--front .wordmark {
    left: 72px;
    top: 230px;
    transform: translateY(-100%);
    font-size: 46px;
    color: var(--forest-text);
  }
  .card--back .wordmark {
    left: 50%;
    top: 196px;
    transform: translate(-50%, -50%);
    font-size: 68px;
    color: #ffffff;
  }

  .divider {
    position: absolute;
    left: 373px;
    top: 114px;
    width: 1px;
    height: 158px;
    background: var(--divider);
  }
  .contact {
    position: absolute;
    left: 400px;
    top: 118px;
    color: var(--ink-grey);
    font-size: 16px;
  }
  .contact__name {
    margin: 0;
    font-family: "Mulish", sans-serif;
    font-weight: 700;
    font-size: 22px;
    color: var(--forest-text);
    line-height: 1.1;
  }
  .contact__role {
    margin: 2px 0 16px;
    line-height: 1.2;
  }
  .contact__list {
    list-style: none;
    margin: 0;
    padding: 0;
  }
  .contact__list li {
    display: flex;
    align-items: center;
    gap: 10px;
    height: 20.5px;
  }
  .contact__list svg { width: 15px; height: 15px; fill: var(--forest); flex: none; }
  .contact__city { margin: 12px 0 0 4px; }
</style>
</head>
<body>
<main class="canvas">
  <section class="card card--front" aria-label="Card front">
    <div class="wordmark">Zub Capital</div>
    <div class="divider"></div>
    <div class="contact">
      <p class="contact__name">Mark Ellison</p>
      <p class="contact__role">Managing Director</p>
      <ul class="contact__list">
        <li>
          <svg viewBox="0 0 16 16" aria-hidden="true"><path d="M3.5 1.5l2.5 0 1 3.5-1.6 1.2c.8 1.8 2.2 3.2 4 4L10.6 8.6l3.4 1v2.6c0 .8-.7 1.5-1.5 1.4C6.6 13 2.9 9.3 2.1 3.5 2 2.4 2.6 1.5 3.5 1.5z"/></svg>
          <span>+41 79555 0148</span>
        </li>
        <li>
          <svg viewBox="0 0 16 16" aria-hidden="true"><path d="M1.5 4h13v8.5h-13z M2.5 5l5.5 4 5.5-4v-.2h-11z" fill-rule="evenodd"/></svg>
          <span>mark@zub.capital</span>
        </li>
        <li>
          <svg viewBox="0 0 16 16" aria-hidden="true"><circle cx="8" cy="8" r="7"/><path d="M5 4.5c1.5 0 2.5 1 2 2.3-.6 1.3-2 1-2.5 2.5-.3 1 .5 2 1 3" stroke="#f5f5f5" stroke-width="1.4" fill="none"/></svg>
          <span>www.zub.capital</span>
        </li>
      </ul>
      <p class="contact__city">Geneva, Switzerland</p>
    </div>
  </section>

  <section class="card card--back" aria-label="Card back">
    <div class="wordmark">Zub Capital</div>
  </section>
</main>
</body>
</html>
```